Letterhead for Conveyancing Company

Use existing logo to create a letterhead for a conveyancing company. Must be able to be used in Microsoft Word. Easy to read and professional.
Contact information to be at the bottom.
Bright Oak Conveyancing Pty Ltd
ACN 621 984 736PO Box 535 Campbelltown SA 5074
Mobile - 0461739286
Web address - www.brightoakconveyancing.com.au

Requirements
Must have
• Logo and contact details.
• Simple and professional.

```html
<!DOCTYPE html>
<html lang="en">
<head>
<meta charset="utf-8">
<title>Bright Oak Conveyancing – Letterhead</title>
<link rel="stylesheet" href="https://fonts.googleapis.com/css2?family=Didact+Gothic&family=Roboto:wght@400;500&display=swap">
<style>
  :root {
    --brand-pink: #e63e92;
    --text-grey: #5f5f5f;
    --heading-grey: #4a4a4a;
    --rule-grey: #c9c9c9;
    --paper: #ffffff;
    --backdrop: #e6e6e6;
  }
  * { box-sizing: border-box; margin: 0; padding: 0; }
  html, body {
    width: 1024px; height: 1200px; overflow: hidden;
    background: var(--backdrop);
  }
  .letterhead {
    position: absolute; left: 83px; top: 0;
    width: 858px; height: 1200px;
    background: var(--paper);
    font-family: "Didact Gothic", "Century Gothic", sans-serif;
    color: var(--text-grey);
  }
  .brand-name {
    position: absolute; left: 60px; top: 104px;
    font-family: "Didact Gothic", "Century Gothic", sans-serif;
    font-weight: 400; font-size: 36px; line-height: 44px;
    color: var(--heading-grey); white-space: nowrap;
  }
  .header-contact {
    position: absolute; left: 535px; top: 84px;
    height: 90px; padding-left: 18px;
    border-left: 1px solid var(--rule-grey);
    font-family: "Roboto", Arial, sans-serif; font-style: normal;
    font-size: 13px; line-height: 18px; color: var(--text-grey);
  }
  .header-contact .company { font-weight: 500; color: var(--heading-grey); }
  .header-contact .phone {
    display: flex; align-items: center; gap: 7px; margin-top: 9px;
  }
  .salutation {
    position: absolute; left: 82px; top: 312px;
    font-size: 20px; font-weight: 400; color: var(--heading-grey);
  }
  .letter-body {
    position: absolute; left: 82px; top: 372px; width: 706px;
    font-size: 13px; line-height: 18px; text-align: justify;
  }
  .letter-body p { margin-bottom: 20px; }
  .sign-off {
    position: absolute; left: 82px; top: 760px; font-size: 13px;
  }
  .signature {
    position: absolute; left: 80px; top: 832px;
    width: 148px; height: 70px;
    background: linear-gradient(180deg, #eef2fa, #dfe6f4);
    border-radius: 4px;
  }
  .footer-band {
    position: absolute; left: 0; right: 0; top: 1132px; height: 29px;
    background: var(--brand-pink);
    display: flex; align-items: center; justify-content: center;
    font-family: "Roboto", Arial, sans-serif;
    font-size: 12.5px; letter-spacing: 3.2px; color: #ffffff;
  }
</style>
</head>
<body>
<main class="letterhead">
  <div class="brand-name">Bright Oak</div>

  <address class="header-contact">
    <div class="company">Bright Oak Conveyancing Pty Ltd</div>
    <div>PO Box 871 Marlowdale SA 5096</div>
    <div>ACN 583 217 469</div>
    <div class="phone">
      <svg width="11" height="11" viewBox="0 0 24 24" aria-hidden="true">
        <path fill="var(--brand-pink)" d="M6.6 10.8a15.1 15.1 0 0 0 6.6 6.6l2.2-2.2a1 1 0 0 1 1-.25 11.4 11.4 0 0 0 3.6.57 1 1 0 0 1 1 1V20a1 1 0 0 1-1 1A17 17 0 0 1 3 4a1 1 0 0 1 1-1h3.5a1 1 0 0 1 1 1c0 1.25.2 2.45.57 3.57a1 1 0 0 1-.25 1z"/>
      </svg>
      <span>0461739286</span>
    </div>
  </address>

  <h1 class="salutation">Dear Mr. Hale,</h1>

  <section class="letter-body">
    <p>Lorem ipsum dolor sit amet, consectetur adipiscing elit. Donec orci purus, luctus vitae dignissim eu, iaculis sed purus. Vivamus faucibus, ipsum nec aliquet viverra, leo mauris condimentum ligula, sit amet sagittis enim ligula quis arcu. Nam egestas tortor id nisi porttitor mattis. In tortor ante, ultricies in suscipit a, tempus non massa. Vivamus et auctor mi. Fusce vel massa nulla. Phasellus nec eros mauris, et scelerisque orci.</p>
    <p>Donec malesuada orci vitae nulla accumsan porta a id massa. Quisque accumsan iaculis magna sit amet fringilla. Maecenas consequat, magna eget tincidunt semper, odio nibh rutrum mi, id feugiat ante nisi eu risus. Vestibulum nunc orci, rhoncus a placerat in, ultricies in mi. Cras mattis varius eros, vel fringilla nisi suscipit eget. Quisque scelerisque sagittis nulla at porttitor.</p>
    <p>Sed id augue vitae urna euismod commodo aliquet a quam. Pellentesque arcu velit, cursus et malesuada ut, consequat et diam. Nullam erat sem, rhoncus id ullamcorper vitae, rhoncus et arcu. In ultricies ultricies nulla, ut rutrum nisi iaculis at. Donec eu magna a metus ornare faucibus. Fusce aliquet faucibus ultricies. Morbi semper, est id tincidunt gravida, sem arcu adipiscing lacus, ac bibendum nulla leo eu purus. Quisque nec diam sed risus consectetur a ccumsan quis quis nibh. Vestibulum id purus lorem.</p>
    <p>It is a long established fact that a reader will be distracted by the readable content of a page when looking at its layout. The point of using Lorem Ipsum is that it has a more-or-less normal distribution of letters, as opposed to using 'Content here, content here', making it look like readable English. Many desktop publishing packages</p>
  </section>

  <div class="sign-off">Sincerely,</div>
  <div class="signature" role="img" aria-label="Handwritten signature of Daniel Hale"></div>

  <footer class="footer-band">www.brightoakconveyancing.com.au</footer>
</main>
</body>
</html>
```